Corvane Business Cards

Front of business card will have logo, name, address, & telephone number. Back of card will have a list of services provided - Roads, Substation Pads, Temporary Pads, Site Pads, Land Leveling, Powerline Row Cleaning, Land Clearing, Gates, Fencing, Construction Entrances, Excavation, Trenching, Underground Utilities, Directional Boring, Pile Driving. We are a construction company that uses heavy equipment like bulldozers, motor graders/blades, dump trucks, backhoes, hydro axes, & skid loaders. We build roads, pads, & install electric utility lines & waterlines underground. This logo is new. The word "Construction" can be smaller as uploaded 2 example edited logos. We will be using this card design for many employees.
Target Market(s)
Industrial Electric Powerline, Wind Turbine, Solar Panel, & Water Utility companies.
Contact Information for Business Card
Name/Position - Dwayne Halster - Owner
Address: 4875 FM 309
Ridgeton, TX 79412
Phone number - (325) 482-5096

```html
<!DOCTYPE html>
<html lang="en">
<head>
<meta charset="utf-8">
<title>Corvane Construction Business Cards</title>
<link rel="stylesheet" href="https://fonts.googleapis.com/css2?family=Arimo:wght@400;700&display=swap">
<style>
  :root {
    --backdrop: #9a6434;
    --maroon: #3a111b;
    --paper: #ffffff;
    --rule: #6b5a66;
    --shadow: rgba(0, 0, 0, 0.45);
  }
  * { margin: 0; padding: 0; box-sizing: border-box; }
  html, body { width: 1200px; height: 900px; overflow: hidden; }
  body {
    position: relative;
    background: var(--backdrop);
    font-family: "Arimo", Arial, sans-serif;
  }
  .card {
    position: absolute;
    width: 556px;
    height: 343px;
    box-shadow: 3px 4px 6px var(--shadow);
    overflow: hidden;
  }
  .card--front { left: 330px; top: 90px; background: var(--maroon); }
  .card--back  { left: 330px; top: 470px; background: var(--maroon); color: var(--paper); }

  .front__top {
    position: absolute; left: 0; top: 0;
    width: 100%; height: 182px;
    background: var(--paper);
  }
  .brand {
    position: absolute;
    display: flex; align-items: center; gap: 16px;
    font-weight: 700;
    letter-spacing: 1px;
    white-space: nowrap;
  }
  .brand__mark { width: 26px; height: 26px; flex: none; }
  .front__top .brand { left: 46px; top: 96px; font-size: 31px; color: var(--maroon); }
  .front__top .brand__mark { background: var(--maroon); }

  .contact-name {
    position: absolute; left: 28px; top: 258px;
    color: var(--paper); font-weight: 700; font-size: 24px;
  }
  .contact-role {
    position: absolute; left: 29px; top: 287px;
    color: var(--paper); font-size: 19px;
  }
  .contact-phone {
    position: absolute; right: 35px; top: 222px;
    color: var(--paper); font-weight: 700; font-size: 22px;
  }
  .contact-address {
    position: absolute; right: 35px; top: 264px;
    color: var(--paper); font-size: 19px; line-height: 25px; text-align: right;
  }

  .back__mark {
    position: absolute; left: 250px; top: 80px;
    width: 56px; height: 56px; background: var(--paper);
  }
  .back__brand {
    position: absolute; left: 60px; top: 185px; width: 436px;
    display: flex; align-items: center; justify-content: center; gap: 10px;
  }
  .back__rule { flex: 1; height: 1px; background: var(--rule); }
  .back__name { font-weight: 700; font-size: 19px; letter-spacing: 1px; white-space: nowrap; }
  .services {
    position: absolute; left: 0; top: 238px; width: 100%;
    text-align: center; font-size: 16px; line-height: 21px;
  }
</style>
</head>
<body>
  <section class="card card--front" aria-label="Business card front">
    <div class="front__top">
      <div class="brand"><span class="brand__mark"></span>CORVANE CONSTRUCTION</div>
    </div>
    <p class="contact-phone">(325) 482-5096</p>
    <p class="contact-name">DWAYNE HALSTER</p>
    <p class="contact-role">Owner</p>
    <p class="contact-address">4875 FM 309<br>Ridgeton, TX 79412</p>
  </section>

  <section class="card card--back" aria-label="Business card back">
    <div class="back__mark"></div>
    <div class="back__brand">
      <span class="back__rule"></span>
      <span class="back__name">CORVANE CONSTRUCTION</span>
      <span class="back__rule"></span>
    </div>
    <p class="services">We are a construction company that uses heavy equipment<br>like bulldozers | motor graders/blades | dump trucks | backhoes<br>hydro axes &amp; skid loaders.</p>
  </section>
</body>
</html>
```